In need of a Wordpress website for a Water Sports Rental Company!

We are starting a new venture that provides a variety of rental equipment in the Cayman Islands. We are in need of a website where guests are able to book their rental gear during their stay in Cayman. We will also have an interactive map where guests can learn about off the beaten path activities to explore in here Cayman.

Our target market is middle/upper class, so we need a website that appeals to this group. We need our website to be clean, simple and easy to navigate. We need it to be highly visual and modern. We like the idea of the website having a tropical feel to it, we are very open to creative ideas that reflects this!

Must be designed in WordPress using the Velmora template I’ve provided.

You will find all instructions & the photos I want to use for this website on the following stashvo account:
- www.stashvo.com
- Username: hello@lumentrips.com
- Password: pelican7

All of the photos will need to be resized accordingly to be as small as possible without loosing resolution.

These are the tabs that will be used:
- Home Page
- Adventure Map
- Rental Gear
- Tours
- Photo Gallery
- Contact Us

Home Page
- You will find all the text and instructions for the home page in the word document named ‘Home Page’.

Adventure Map
- You will find all the text and instructions for the home page in the word document named ‘Adventure Map Content’
- There will also be a few 'guide' pages under this tab, which we will go in to detail with the winner.

Rentals
- You will find all the text and instructions for the Rentals page in the word document named ‘Rentals Content’

Tours
- This will just be a page saying ‘kayaking, snorkeling & Bioluminescence tours coming soon’.

Photo Gallery
- You will find the photos for this in our Stashvo.com Account

Contact Us
- Send us a Message – page will be similar to our other site http://lumentrips.com/contact/
- Phone: +1 (345) 555 0192
- Email: hello@tidalotterco.com

The big factors on who will have the winning design are:
- The background used
- The layout of the Home Page
- The animations at the top of the Rental Landing Page
- The overall clean, professional look to the website

If you have any questions, don't hesitate to ask.

We look forward to working with you all!!

Good luck!!

Target Market(s)

Middle/Upper Class on vacation with their family

Industry/Entity Type

It Company

Coding

Coded - Design and coding required

Number of Pages Required

5+ page

Colors
fffbf0
cadf82
fbf289
f6faec
fdf9cf
eaf2ce
fff3d1
fee18a
abd037

Requirements
Must have
• - Must be designed in Wordpress using the Velmora template I have provided or another suitable web template.
• - Must be Responsive Web Design so that the website adjusts to various screen sizes.

```html
<!DOCTYPE html>
<html lang="en">
<head>
<meta charset="utf-8">
<title>Tidal Otter – Cayman's Premier Adventure and Rental Company</title>
<link rel="stylesheet" href="https://fonts.googleapis.com/css2?family=Lato:wght@300;400;700;900&family=Kaushan+Script&display=swap">
<style>
:root{
  --lime:#abd037;
  --lime-soft:#cadf82;
  --lime-pale:#eaf2ce;
  --cream:#fffbf0;
  --sand:#d9c6a3;
  --sand-dark:#c8b38c;
  --teal:#1fa99a;
  --teal-dark:#158c80;
  --ink:#333333;
  --muted:#666666;
  --white:#ffffff;
  --footer:#3a3a3a;
  --footer-deep:#2c2c2c;
  --script:#3a9a52;
}
*{box-sizing:border-box;margin:0;padding:0}
html,body{width:1200px;height:4905px;overflow:hidden}
body{position:relative;font-family:'Lato',sans-serif;color:var(--ink);
  background:linear-gradient(180deg,var(--sand) 0%,var(--sand-dark) 50%,var(--sand) 100%)}
.abs{position:absolute}

/* nav */
.main-nav{position:absolute;top:0;left:0;width:1200px;height:58px;background:var(--lime);display:flex;justify-content:center}
.main-nav a{display:flex;align-items:center;padding:0 40px;color:var(--white);font-size:14px;font-weight:700;text-decoration:none;letter-spacing:.5px;border-right:1px solid rgba(255,255,255,.35)}
.main-nav a:first-child{border-left:1px solid rgba(255,255,255,.35)}

/* hero */
.hero{position:absolute;top:58px;left:0;width:1200px;height:808px;
  background:linear-gradient(180deg,#5f8fb5 0%,#8fb6cf 25%,#3cb4bd 45%,#1f8e9e 70%,#c9b48a 100%)}
.brand{position:absolute;top:135px;left:0;width:1200px;display:flex;justify-content:center;align-items:center;gap:14px}
.brand-dot{width:34px;height:34px;border-radius:50%;background:var(--lime)}
.brand-name{font-family:'Lato',sans-serif;font-weight:900;font-size:34px;color:var(--white);letter-spacing:1px}
.hero h1{position:absolute;top:315px;width:1200px;text-align:center;font-weight:400;font-size:66px;letter-spacing:6px;color:var(--white)}
.hero .tagline{position:absolute;top:405px;width:1200px;text-align:center;font-size:28px;font-weight:300;letter-spacing:2px;color:var(--white)}
.hero .btn-ghost{position:absolute;top:470px;left:517px;width:166px;height:52px;border:2px solid var(--lime);color:var(--white);font-size:15px;letter-spacing:1px;display:flex;align-items:center;justify-content:center;background:rgba(0,0,0,.15)}
.hero .arrow{position:absolute;top:370px;width:40px;height:40px;border:2px solid rgba(255,255,255,.6);border-radius:50%}
.hero .arrow.left{left:30px}.hero .arrow.right{right:30px}
.hero .arrow svg{width:36px;height:36px}

/* pillars */
.pillar{position:absolute;top:575px;width:330px}
.pillar .photo{width:330px;height:330px;border-radius:50%;border:6px solid var(--white);margin:0 auto}
.pillar .card{margin-top:15px;background:var(--white);height:200px;padding:28px 26px;text-align:center}
.pillar h3{font-size:22px;font-weight:400;letter-spacing:2px;margin-bottom:16px}
.pillar p{font-size:11px;line-height:1.7;color:var(--muted)}

/* welcome */
.welcome{position:absolute;top:1154px;left:82px;width:1036px;height:317px;background:var(--lime-soft);border:3px dashed rgba(255,255,255,.7);outline:8px solid var(--lime-soft);text-align:center;padding:40px 40px}
.welcome h2{font-size:34px;font-weight:400;letter-spacing:2px;color:var(--ink)}
.welcome .script{display:block;font-family:'Kaushan Script',cursive;font-size:34px;color:var(--script);margin:6px 0 22px}
.welcome p{font-size:13px;line-height:1.8;color:var(--ink)}

/* features */
.feature .photo{position:absolute;width:525px;height:315px;border:5px solid var(--white)}
.feature .card{position:absolute;width:510px;height:285px;background:var(--white);padding:38px 42px}
.feature h3{font-size:18px;font-weight:400;line-height:1.35;margin-bottom:16px;color:var(--ink)}
.feature p{font-size:11px;line-height:1.7;color:var(--muted);margin-bottom:22px}
.btn-line{display:inline-flex;align-items:center}
.btn-line span{border:1px solid var(--teal);padding:10px 20px;font-size:13px;color:var(--ink)}
.btn-line i{display:inline-block;width:70px;height:1px;background:var(--teal);margin-left:8px}

/* picks */
.picks{position:absolute;top:4015px;left:0;width:1200px;height:548px;background:var(--lime-soft);text-align:center}
.picks h2{margin-top:40px;font-size:36px;font-weight:400;letter-spacing:2px}
.picks .script{display:block;font-family:'Kaushan Script',cursive;font-size:36px;color:var(--script);margin-top:2px}
.pick{position:absolute;top:180px;width:245px;text-align:center}
.pick .photo{width:245px;height:158px}
.pick h4{margin-top:22px;font-size:24px;font-weight:700}
.pick p{font-size:12px;line-height:1.5;margin:10px 6px 14px}
.pick .btn{display:inline-block;border:1px solid var(--teal);padding:8px 20px;font-size:11px;font-weight:700;background:var(--white)}

.tweet-bar{position:absolute;top:4568px;left:0;width:1200px;height:38px;background:var(--teal);color:var(--white);font-size:12px;font-style:italic;display:flex;align-items:center;justify-content:center;gap:12px}

/* footer */
.site-footer{position:absolute;top:4606px;left:0;width:1200px;height:299px;background:var(--footer);color:#dddddd}
.site-footer .f-brand{position:absolute;top:30px;left:90px;display:flex;align-items:center;gap:10px}
.f-brand .dot{width:22px;height:22px;border-radius:50%;background:var(--lime)}
.f-brand span{font-weight:900;font-size:20px;color:var(--white)}
.f-about{position:absolute;top:95px;left:82px;width:170px;font-size:12px;line-height:1.5;display:flex;gap:10px}
.f-phone{position:absolute;top:160px;left:82px;font-size:13px;font-weight:700;display:flex;gap:10px;align-items:center}
.f-col{position:absolute;top:30px}
.f-col h5{font-size:14px;font-weight:400;color:var(--white);margin-bottom:16px}
.f-col li{list-style:none;font-size:10px;letter-spacing:.5px;margin-bottom:12px;display:flex;align-items:center;gap:10px}
.f-col li::before{content:"";width:5px;height:5px;border-top:1.5px solid var(--lime);border-right:1.5px solid var(--lime);transform:rotate(45deg)}
.f-form input{display:block;width:160px;height:24px;margin-bottom:8px;border:1px solid #888;background:#444;color:#ccc;font-size:10px;padding:0 8px;font-family:inherit}
.f-form button{width:160px;height:26px;background:var(--teal);border:0;color:var(--white);font-size:11px;font-weight:700;font-family:inherit}
.f-bottom{position:absolute;bottom:0;left:0;width:1200px;height:40px;background:var(--footer-deep);display:flex;align-items:center;justify-content:space-between;padding:0 82px;font-size:11px;color:#aaaaaa}
.f-bottom .social{display:flex;gap:12px}
.f-bottom .social i{width:14px;height:14px;border-radius:50%;background:#bbbbbb;display:block}
</style>
</head>
<body>

<nav class="main-nav">
  <a>HOME</a><a>ADVENTURE MAP</a><a>RENTAL GEAR</a><a>TOURS</a><a>PHOTO GALLERY</a><a>CONTACT US</a>
</nav>

<header class="hero" role="img" aria-label="Tropical beach photo: kayakers on turquoise water near a sandy shore under a blue sky">
  <div class="brand"><span class="brand-dot"></span><span class="brand-name">TIDAL OTTER</span></div>
  <h1>CAYMAN'S</h1>
  <p class="tagline">PREMIER ADVENTURE AND RENTAL COMPANY</p>
  <span class="btn-ghost">LEARN MORE</span>
  <span class="arrow left"><svg viewBox="0 0 36 36"><path d="M21 11l-7 7 7 7" stroke="#fff" stroke-width="2" fill="none"/></svg></span>
  <span class="arrow right"><svg viewBox="0 0 36 36"><path d="M15 11l7 7-7 7" stroke="#fff" stroke-width="2" fill="none"/></svg></span>
</header>

<section class="pillar" style="left:82px">
  <div class="photo" role="img" aria-label="Circular photo of two people kayaking in clear water" style="background:radial-gradient(circle at 50% 40%,#7fd3dc,#2a9fb3 70%,#7fb0c9)"></div>
  <div class="card"><h3>EXPLORATION</h3><p>Rent everything you need to get outside and explore the island on your own terms. Snorkel the Kittiwake, check out the bioluminescence and much more with your own gear!</p></div>
</section>
<section class="pillar" style="left:435px">
  <div class="photo" role="img" aria-label="Circular photo of a person relaxing on a float in calm blue water" style="background:radial-gradient(circle at 50% 50%,#5cc7d6,#1a86a8 75%)"></div>
  <div class="card"><h3>RELAXATION</h3><p>We will come straight to your resort or condo and set everything up for you and your family to enjoy our kayaks and paddle boards on the beautiful calm waters off Seven Mile Beach.</p></div>
</section>
<section class="pillar" style="left:788px">
  <div class="photo" role="img" aria-label="Circular photo of a tropical palm plant against a blue sky" style="background:radial-gradient(circle at 50% 55%,#8aa23c,#4f8f5a 55%,#6fb3d9)"></div>
  <div class="card"><h3>EDUCATION</h3><p>We love sharing our knowledge on Cayman's history and the island's rich and endless marine life. We'll also teach you everything you need to find those secluded spots on your adventures.</p></div>
</section>

<section class="welcome">
  <h2>WELCOME TO</h2>
  <span class="script">Tidal Otter!</span>
  <p>We love having the freedom to explore when travelling and we bet you do to! We are Grand Cayman's premier rental company, offering everything you need to make the most of your vacation. Our website serves as a great starting point to help you prepare for your vacation here in Cayman. We feature a huge selection of adventures on our interactive map with tons of useful information, pictures and directions. Our adventure map is the perfect guide to all our great spots to check out here in Cayman.</p>
</section>

<!-- feature 1 -->
<section class="feature abs" style="top:1537px;left:0;width:1200px;height:330px">
  <div class="photo" style="left:82px;top:0;background:linear-gradient(180deg,#9cc9df,#3fc1c9 45%,#1b98ae)" role="img" aria-label="Aerial photo of paddle boarders on turquoise shallow water"></div>
  <div class="card" style="left:602px;top:25px">
    <h3>Your one stop shop for all the rentals<br>you need here in Cayman!</h3>
    <p>We have a huge array of fun toys and equipment for you to enjoy. Whether it's for exploring or relaxing, we have all the equipment you need to make the most of your trip here in Cayman. Need something that we don't stock, just ask and we'll do everything we can to get you the gear you need!</p>
    <span class="btn-line"><span>Learn More</span><i></i></span>
  </div>
</section>

<!-- feature 2 -->
<section class="feature abs" style="top:1887px;left:0;width:1200px;height:330px">
  <div class="card" style="left:88px;top:25px">
    <h3>Check out our interactive<br>map of Cayman!</h3>
    <p>You won't find any tourist traps on our map! We're all about getting off the beaten path and finding those unique spots and natural wonders to explore. Get our expert advice on which adventures are best for you and how to tackle them!</p>
    <span class="btn-line"><span>Learn More</span><i></i></span>
  </div>
  <div class="photo" style="left:594px;top:0;background:linear-gradient(135deg,#7fd0e6,#a9dcec 50%,#6fc4df)" role="img" aria-label="Illustrated map of Grand Cayman with adventure location markers"></div>
</section>

<!-- feature 3 -->
<section class="feature abs" style="top:2240px;left:0;width:1200px;height:330px">
  <div class="photo" style="left:82px;top:0;background:linear-gradient(180deg,#8ec6e0,#6ab6c9 50%,#2d93a8)" role="img" aria-label="Photo of two people paddling a clear inflatable kayak"></div>
  <div class="card" style="left:602px;top:25px">
    <h3>Enjoy Complete<br>freedom to explore.</h3>
    <p>Inflatable kayaks have revolutionized the way kayak exploration is done in a way never before. Our kayaks give you the freedom to explore Cayman's most secluded locations and uncover those hard to reach reefs. Our kayaks are light, comfortable and easy to use.</p>
    <span class="btn-line"><span>Learn More</span><i></i></span>
  </div>
</section>

<!-- feature 4 -->
<section class="feature abs" style="top:2600px;left:0;width:1200px;height:330px">
  <div class="card" style="left:88px;top:25px">
    <h3>There's no easier way to get around the island.</h3>
    <p>What better way is there to explore the island other than to rent a bike and go? Our cruiser bikes are perfect for those interested in heading out on a full day adventure. If you're looking for something more casual, renting a cruiser is perfect to get around the Seven Mile Beach area. Use our map to help guide you to all our suggested locations to explore!</p>
    <span class="btn-line"><span>Learn More</span><i></i></span>
  </div>
  <div class="photo" style="left:594px;top:0;background:linear-gradient(180deg,#9fd3ea,#d8cbb0 60%,#b99f7c)" role="img" aria-label="Photo of two cruiser bicycles parked on a beach"></div>
</section>

<!-- feature 5 -->
<section class="feature abs" style="top:2959px;left:0;width:1200px;height:330px">
  <div class="photo" style="left:82px;top:0;background:linear-gradient(180deg,#6fa9d6,#49bccb 45%,#e8dcc0)" role="img" aria-label="Photo of a kayak resting on a white sand beach by clear water"></div>
  <div class="card" style="left:602px;top:25px">
    <h3>We want to be your personal concierge<br>and help you to plan out your trip!</h3>
    <p>When we come to deliver your equipment, we teach you everything you need to know about the island including the best hidden spots, best restaurants &amp; bars to eat &amp; drink and anything else you might be curious about. Please don't hesitate to contact us for any and all of your vacation questions. We are happy to help!</p>
    <span class="btn-line"><span>Learn More</span><i></i></span>
  </div>
</section>

<!-- feature 6 -->
<section class="feature abs" style="top:3313px;left:0;width:1200px;height:330px">
  <div class="card" style="left:88px;top:25px">
    <h3>Is it a boat? Is it a whale?.... It's a Floatnest!</h3>
    <p>Easily one of the coolest inventions we've ever come across, the Floatnest is a versatile toy the whole family can enjoy together. Spend the day cruising along Seven Mile Beach in style as you bar hop with your clan. Better still, bring a cooler on board and put the kids to work paddling as you relax in your hammock on the crystal clear waters!</p>
    <span class="btn-line"><span>Learn More</span><i></i></span>
  </div>
  <div class="photo" style="left:594px;top:0;background:linear-gradient(180deg,#4aa6c4,#2c8aa9 50%,#1f6f8f)" role="img" aria-label="Aerial photo of colourful floating hammock boats on blue water"></div>
</section>

<!-- feature 7 -->
<section class="feature abs" style="top:3662px;left:0;width:1200px;height:330px">
  <div class="photo" style="left:82px;top:0;background:linear-gradient(180deg,#49b6cc,#2a9dbb 50%,#1a7fa3)" role="img" aria-label="Underwater photo of a snorkeler wearing a full face mask"></div>
  <div class="card" style="left:602px;top:25px">
    <h3>A new way to Snorkel!</h3>
    <p>Our full face snorkel masks are easy to use, making them perfect for kids and beginners. You simply put the mask on and breath as you usually would. There's no need to get used to breathing from your mouth and you don't experience a sore jaw from having to hold the mouth piece in place. Just ask and we'll bring one along for you to try!</p>
    <span class="btn-line"><span>Learn More</span><i></i></span>
  </div>
</section>

<section class="picks">
  <h2>OUR ADVENTURE</h2>
  <span class="script">Top-Picks</span>
  <div class="pick" style="left:82px">
    <div class="photo" role="img" aria-label="Night photo of glowing blue bioluminescent water" style="background:linear-gradient(180deg,#0b1b3a,#1b5fa8 60%,#0d2a55)"></div>
    <h4>BIO BAY</h4><p>Lorem Ipsum is simply dummy text of the printing and typesetting industry</p><span class="btn">LEARN MORE</span>
  </div>
  <div class="pick" style="left:348px">
    <div class="photo" role="img" aria-label="Underwater photo of a shipwreck dive site" style="background:linear-gradient(180deg,#4fb6c4,#2f8b98 60%,#1d6673)"></div>
    <h4>KITTIWAKE</h4><p>Lorem Ipsum is simply dummy text of the printing and typesetting industry</p><span class="btn">LEARN MORE</span>
  </div>
  <div class="pick" style="left:614px">
    <div class="photo" role="img" aria-label="Aerial photo of a small sandy island surrounded by turquoise water" style="background:linear-gradient(180deg,#5aa8d0,#48c7cf 55%,#e4e0c6)"></div>
    <h4>SAND CAY ISLAND</h4><p>Lorem Ipsum is simply dummy text of the printing and typesetting industry</p><span class="btn">LEARN MORE</span>
  </div>
  <div class="pick" style="left:880px">
    <div class="photo" role="img" aria-label="Aerial photo of shallow sandbar water with swimmers" style="background:linear-gradient(180deg,#7cc8d8,#3aa9be 55%,#2a7f9c)"></div>
    <h4>STINGRAY CITY</h4><p>Lorem Ipsum is simply dummy text of the printing and typesetting industry</p><span class="btn">LEARN MORE</span>
  </div>
</section>

<div class="tweet-bar">
  <svg width="14" height="14" viewBox="0 0 14 14"><path d="M2 3h10v6H6l-3 3V9H2z" fill="#fff"/></svg>
  <span>Lorem ipsum dolor sit amet, consectetur adipiscing elit. Morbi adipiscing gravida odio, sit amet suscipit risus ultrices eu.</span>
</div>

<footer class="site-footer">
  <div class="f-brand"><span class="dot"></span><span>TIDAL OTTER</span></div>
  <div class="f-about">
    <svg width="12" height="16" viewBox="0 0 12 16"><path d="M6 0a6 6 0 0 1 6 6c0 4-6 10-6 10S0 10 0 6a6 6 0 0 1 6-6z" fill="#dddddd"/><circle cx="6" cy="6" r="2.2" fill="#3a3a3a"/></svg>
    <span>It is a long established fact that a reader will be distracted by the</span>
  </div>
  <div class="f-phone">
    <svg width="14" height="14" viewBox="0 0 14 14"><path d="M3 1l2.5 3-1.5 1.5c.8 1.8 2.2 3.2 4 4L9.5 8 13 10.5 11.5 13C6 13 1 8 1 2.5z" fill="#dddddd"/></svg>
    <span>+1 (345) 555 0192</span>
  </div>
  <div class="f-col" style="left:410px">
    <h5>Quick Links</h5>
    <ul><li>HOME</li><li>ADVENTURE MAP</li><li>RENTAL GEAR</li><li>TOURS</li><li>PHOTO GALLERY</li><li>CONTACT US</li></ul>
  </div>
  <div class="f-col" style="left:660px">
    <h5>Our Adventures</h5>
    <ul><li>BIO BAY</li><li>KITTIWAKE</li><li>SAND CAY ISLAND</li><li>STINGRAY CITY</li></ul>
  </div>
  <div class="f-col f-form" style="left:948px">
    <h5>Contact Us</h5>
    <input placeholder="Name"><input placeholder="Email"><input placeholder="Phone">
    <button>SUBMIT</button>
  </div>
  <div class="f-bottom">
    <span>tidalotterco.com©2017. All rights reserved</span>
    <span class="social"><i></i><i></i><i></i><i></i><i></i></span>
  </div>
</footer>

</body>
</html>
```